Health and Fitness Club requires a stunning and simple website

We are a health and fitness club based in Dubai, when we launch we will be the biggest club in the country, we will also have the 2 largest activity rooms in the country, we are setting a new standard in the industry by offering one thing, our attitude.

Our attitude means the following:
unlike other clubs we have no hidden charges or fees
our members can join daily, monthly, 6 months or annually
our service and facility are comparable to 5* hotel gyms
our equipment is second to none
our space is the biggest in the country
we do not force our members to use our in-house personal trainers - you can bring your own and we will not charge them entry!
we will have a cutting edge brawnmesh box in our gym with classes by the best trainers in the country
we will be providing free-lance personal trainers a platform to engage customers, grow their business and even use our activity rooms for classes

Basically we will be a gym like no other, simply because we are gym people and we hate the restrictive practices and hidden charges by other gyms, so we are making our own gym which focuses on quality and service.

All of this has to be communicated in the style of the website, the colors of the website we want to be limited to the logo colors as this will be the same theme running throughout the gym.

The landing page of the website HAS to incorporate elements from our social media presences, this basically is the usual, chirplo, snapvault, kinwall. We can have these as a sidebar, the centre of the page should display the latest article from our blog (also on the website) Also we need to have a calendar for activities and classes on the front page. The menu should have links to the following:
Latest News
About us
Team
Gallery
Membership
Classes
Member Log In
Contact Us
Location

The style of the website has to be similar to the logo, particularly in terms of the fonts used.

```html
<!DOCTYPE html>
<html lang="en">
<head>
<meta charset="utf-8">
<title>Ironvale Fitness</title>
<link href="https://fonts.googleapis.com/css2?family=Oswald:wght@500;700&family=Arimo:wght@400;700&display=swap" rel="stylesheet">
<style>
:root{
  --red:#c8000e;
  --red-dark:#8d0008;
  --black:#0b0b0b;
  --ink:#333;
  --muted:#555;
  --line:#d6d6d6;
  --panel-border:#d9d9d9;
  --footer:#1e1e1e;
  --white:#fff;
}
*{margin:0;padding:0;box-sizing:border-box}
html,body{width:952px;height:1200px;overflow:hidden;background:var(--white)}
body{position:relative;font-family:"Arimo",Arial,sans-serif;color:var(--ink);font-size:9px}
.abs{position:absolute}

.brand{left:143px;top:10px;display:flex;align-items:center;gap:8px}
.brand-dot{width:46px;height:46px;border-radius:50%;background:var(--red)}
.brand-name{font-family:"Oswald",sans-serif;font-weight:700;font-size:17px;color:var(--black);text-transform:uppercase}

.search{left:592px;top:26px;width:210px;height:27px;display:flex}
.search-input{flex:1;border:1px solid #ccc;font-family:"Oswald",sans-serif;font-size:7px;color:#777;padding:9px 10px;text-transform:uppercase}
.search-btn{width:70px;background:var(--black);color:var(--white);font-family:"Oswald",sans-serif;font-weight:700;font-size:9px;display:flex;align-items:center;justify-content:center;text-transform:uppercase;letter-spacing:.5px}

.nav{left:124px;top:82px;width:703px;height:24px;background:var(--red);border-bottom:2px solid var(--red-dark);display:flex;align-items:center;padding-left:20px}
.nav a{font-family:"Oswald",sans-serif;font-weight:700;font-size:8.5px;color:var(--white);text-decoration:none;margin-right:24px}

.slider{left:124px;top:118px;width:703px;height:246px;border:1px solid var(--panel-border);padding:2px}
.slide{position:relative;width:697px;height:240px;background:var(--black);overflow:hidden}
.slide-photo{position:absolute;left:360px;top:0;width:337px;height:229px;background:radial-gradient(ellipse at 50% 55%,#6e6e6e 0%,#2a2a2a 35%,#0b0b0b 65%)}
.slide-band{position:absolute;left:0;bottom:0;width:100%;height:10px;background:var(--red)}
.slide-title{position:absolute;left:40px;top:64px;font-family:"Oswald",sans-serif;font-weight:700;font-size:14px;color:var(--red)}
.slide-text{position:absolute;left:41px;top:90px;width:300px;color:var(--white);font-size:10.2px;line-height:16px}
.slide-btn{position:absolute;left:141px;top:158px;width:85px;height:26px;background:var(--red);border-radius:3px;color:var(--white);font-family:"Oswald",sans-serif;font-weight:700;font-size:11px;display:flex;align-items:center;justify-content:center}
.arrow{position:absolute;top:100px}

.bar{height:23px;background:var(--black);border-top:2px solid #333;color:var(--white);font-family:"Oswald",sans-serif;font-weight:700;font-size:12.5px;padding-left:15px;line-height:21px}

.welcome-img{left:125px;top:427px;width:120px;height:92px;background:linear-gradient(135deg,#8a8f96,#c9b9a8 50%,#6f7278)}
.welcome-text{left:263px;top:430px;width:564px;font-size:8.6px;line-height:14.7px;color:var(--ink)}
.welcome-text p+p{margin-top:4px}

.calendar{left:125px;top:592px;width:207px;height:152px;background:#1b1b1b;box-shadow:0 1px 3px rgba(0,0,0,.3)}
.cal-head{height:25px;background:linear-gradient(#d4000f,#a5000b);color:var(--white);font-family:"Oswald",sans-serif;font-weight:700;font-size:12px;text-align:center;line-height:25px}
.cal-days,.cal-grid{display:grid;grid-template-columns:repeat(7,1fr);padding:0 5px}
.cal-days{height:22px;background:#2f2f2f;align-items:center;text-align:center;color:#e0b03a;font-size:9.5px}
.cal-grid{padding-top:7px;row-gap:7px;text-align:center;color:var(--white);font-size:7.5px;font-weight:700}
.cal-grid span{display:inline-block;margin:0 auto;width:13px;height:12px;line-height:12px}
.cal-grid .mark{background:#666}

.cal-divider{left:354px;top:592px;width:1px;height:152px;background:var(--line)}
.events{left:380px;top:598px;width:192px;list-style:none}
.events li{position:relative;padding-left:15px;font-size:8.6px;line-height:13px;color:var(--muted);margin-bottom:13px}
.events li::before{content:"";position:absolute;left:0;top:3px;width:6px;height:6px;background:#ddd}

.article{width:202px}
.art-img{width:202px;height:68px;border:1px solid var(--panel-border);padding:5px}
.art-img div{width:100%;height:100%}
.art-title{font-family:"Oswald",sans-serif;font-weight:700;font-size:10.5px;color:var(--black);margin-top:6px}
.art-date{display:flex;align-items:center;gap:6px;color:var(--red);font-size:8.5px;margin-top:4px}
.art-text{font-size:8.6px;line-height:13.5px;color:var(--muted);margin-top:5px;padding-left:2px}

.panel{left:618px;width:209px;border:1px solid var(--panel-border);box-shadow:0 1px 2px rgba(0,0,0,.1);overflow:hidden}
.panel .bar{font-size:11.5px;padding-left:9px}
.tweets{padding:10px 22px 0 19px}
.tweet{font-size:9.4px;line-height:13px;color:var(--ink)}
.tweet-time{color:var(--red);font-size:9.4px;margin:4px 0 0 1px;padding-bottom:6px;border-bottom:1px solid #bbb;margin-right:-8px}
.tweet+.tweet{margin-top:9px}
.tweet:last-child .tweet-time{border:0}

.wall{padding:6px 10px 0 10px}
.wall-title{font-size:8.7px;font-weight:700;color:#222;display:inline-block;border-bottom:1px solid #333;padding-bottom:2px;padding-right:14px}
.wall-row{display:flex;gap:8px;margin-top:5px;align-items:flex-start}
.wall-thumb{width:38px;height:38px;flex:none}
.wall-text{font-size:8.6px;line-height:13px;color:var(--muted);padding-top:5px}
.wall-sep{height:1px;background:#ccc;margin:8px 30px 7px 0}

.snaps{display:grid;grid-template-columns:repeat(4,38px);gap:10px 12px;padding:12px 10px 0 11px}
.snaps div{width:38px;height:38px;border:1px solid var(--panel-border);padding:3px}
.snaps div i{display:block;width:100%;height:100%}

.footer{left:0;top:1126px;width:952px;height:74px;background:var(--footer);border-top:4px solid var(--red)}
.foot-links{left:125px;top:1152px;font-size:8.5px;color:#ddd}
.foot-copy{left:124px;top:1174px;font-size:8.5px;color:#ddd}
.socials{left:704px;top:1150px;display:flex;gap:8px}
.socials span{width:23px;height:23px;border-radius:50%}
</style>
</head>
<body>

<div class="abs brand"><span class="brand-dot"></span><span class="brand-name">Ironvale Fitness</span></div>

<div class="abs search"><div class="search-input">Enter search ...</div><div class="search-btn">Search</div></div>

<nav class="abs nav">
  <a>Home</a><a>About us</a><a>Latest News</a><a>Team</a><a>Gallery</a><a>Membership</a><a>Classes</a><a>Member Log In</a><a>Contact Us</a><a>Location</a>
</nav>

<section class="abs slider">
  <div class="slide">
    <div class="slide-photo" role="img" aria-label="Black and white photo of a muscular man flexing, seen from behind"></div>
    <div class="slide-band"></div>
    <svg class="arrow" style="left:14px" width="12" height="22" viewBox="0 0 12 22"><path d="M11 1 1 11l10 10" fill="none" stroke="#555" stroke-width="1.5"/></svg>
    <svg class="arrow" style="left:670px" width="12" height="22" viewBox="0 0 12 22"><path d="M1 1l10 10L1 21" fill="none" stroke="#555" stroke-width="1.5"/></svg>
    <h1 class="slide-title">Vestibulum ante ipsum primis in faucibus orci</h1>
    <p class="slide-text">Vestibulum ante ipsum primis in faucibus orci luctus et ultrices posuere cubilia Curae; Sed interdum lacus ac lectus fermentum sed sagittis velit sceleri</p>
    <div class="slide-btn">Read more</div>
  </div>
</section>

<h2 class="abs bar" style="left:124px;top:386px;width:703px">Welcome to Ironvale Fitness</h2>
<div class="abs welcome-img" role="img" aria-label="Photo of a person lifting a dumbbell in the gym"></div>
<div class="abs welcome-text">
  <p>Ironvale Fitness Club is a new kind of gym in Dubai, built by gym people who were tired of hidden charges, fixed contracts and restrictive rules. Members can join daily, monthly, for six months or for a full year, and our service and facilities are on par with the best hotel gyms. With the two largest activity rooms in the country, equipment that is second to none and space to train freely, we set a new standard for quality and service.</p>
  <p>Bring your own personal trainer at no extra charge, join classes in our training box led by top coaches, or use our rooms to grow your own training business with us.</p>
</div>

<h2 class="abs bar" style="left:124px;top:549px;width:462px">FITNESS CALENDER</h2>
<div class="abs calendar">
  <div class="cal-head">January, 2014</div>
  <div class="cal-days"><span>S</span><span>M</span><span>T</span><span>W</span><span>T</span><span>F</span><span>S</span></div>
  <div class="cal-grid">
    <span>28</span><span>29</span><span>30</span><span>31</span><span>1</span><span>2</span><span>3</span>
    <span>4</span><span>5</span><span>6</span><span>7</span><span>8</span><span>9</span><span>10</span>
    <span>11</span><span class="mark">12</span><span>13</span><span>14</span><span>15</span><span>16</span><span>17</span>
    <span>18</span><span>19</span><span class="mark">20</span><span>21</span><span>22</span><span>23</span><span class="mark">24</span>
    <span>25</span><span>26</span><span>27</span><span>28</span><span>29</span><span class="mark">30</span><span>31</span>
  </div>
</div>
<div class="abs cal-divider"></div>
<ul class="abs events">
  <li>Donec luctus nisl in nibh ultricies quis convallis justo convallis. Fusce mattis mauris id enim.</li>
  <li>Donec luctus nisl in nibh ultricies quis convallis justo convallis. Fusce mattis mauris id enim.</li>
  <li style="margin-top:20px">Donec luctus nisl in nibh ultricies quis convallis justo convallis. Fusce mattis mauris id enim.</li>
</ul>

<h2 class="abs bar" style="left:124px;top:770px;width:462px;font-size:13.5px">Latest Articles</h2>

<svg width="0" height="0" style="position:absolute"><symbol id="clock" viewBox="0 0 12 12"><circle cx="6" cy="6" r="5" fill="none" stroke="#c8000e" stroke-width="1.6"/><path d="M6 3v3h2.5" fill="none" stroke="#c8000e" stroke-width="1.4"/></symbol></svg>

<article class="abs article" style="left:126px;top:810px">
  <div class="art-img"><div role="img" aria-label="Photo of a man doing a bench press" style="background:linear-gradient(90deg,#9a9a9a,#2a2a2a 40%,#d9c4b3 75%,#aaa)"></div></div>
  <h3 class="art-title">Fusce adipiscing commodo</h3>
  <div class="art-date"><svg width="12" height="12"><use href="#clock"/></svg>May 25th 2013</div>
  <p class="art-text">Proin est enim, modo in, ultrices at dolor. Proin aliquam risus eu sed adipiscing convallis [...]</p>
</article>
<article class="abs article" style="left:364px;top:810px">
  <div class="art-img"><div role="img" aria-label="Photo of a hand holding a dumbbell against a blue background" style="background:linear-gradient(90deg,#1f5fbf,#b08870 35%,#222 55%,#1f5fbf)"></div></div>
  <h3 class="art-title">Nullam portitor enim id dui</h3>
  <div class="art-date"><svg width="12" height="12"><use href="#clock"/></svg>April 22nd 2013</div>
  <p class="art-text">Maecenas vitae felis eu lacus rhoncus pellentesque. Nullam maecenas vitae felis eu</p>
</article>
<article class="abs article" style="left:126px;top:958px">
  <div class="art-img"><div role="img" aria-label="Close-up photo of a hand gripping a dumbbell" style="background:linear-gradient(90deg,#3a3a3a,#777 30%,#d8c0ac 55%,#444)"></div></div>
  <h3 class="art-title">Donec non sapien eu orci ultri</h3>
  <div class="art-date"><svg width="12" height="12"><use href="#clock"/></svg>May 25th 2013</div>
  <p class="art-text">Donec non sapien eu orci ultrices ultrices. Pellentesque vulputate nisl in nunc vestibulum</p>
</article>
<article class="abs article" style="left:364px;top:958px">
  <div class="art-img"><div role="img" aria-label="Photo of a man training on a gym machine" style="background:linear-gradient(90deg,#2b2b2b,#2850a8 25%,#e3a640 45%,#eee 55%,#2850a8 75%,#2b2b2b)"></div></div>
  <h3 class="art-title">Cras ligula neque, pellentesque</h3>
  <div class="art-date"><svg width="12" height="12"><use href="#clock"/></svg>April 22nd 2013</div>
  <p class="art-text">Cras ligula neque, pellentesque eu volutpat eget, tempus id lacus. Sed eros massa [...]</p>
</article>

<aside class="abs panel" style="top:549px;height:168px">
  <h2 class="bar">Latest from Chirplo</h2>
  <div class="tweets">
    <div class="tweet">Donec luctus nisl in nibh ultricies quis convallis justo convallis. Fusce mattis mauris id enim.<div class="tweet-time">2-days ago</div></div>
    <div class="tweet">Convallis. Fusce mattis mauris id enim. Magnust nibh dolorest onlso at quist mattiest.<div class="tweet-time">4-days ago</div></div>
  </div>
</aside>

<aside class="abs panel" style="top:734px;height:166px">
  <h2 class="bar">Kinwall</h2>
  <div class="wall">
    <div class="wall-title">Nullam portitor enim id dui</div>
    <div class="wall-row"><div class="wall-thumb" role="img" aria-label="Photo of a muscular torso" style="background:linear-gradient(135deg,#111,#666 60%,#222)"></div><div class="wall-text">Maecenas vitae felis eu lacus vitae rhoncus pellentesque [...]</div></div>
    <div class="wall-sep"></div>
    <div class="wall-title">Nam eget velit purus nam</div>
    <div class="wall-row"><div class="wall-thumb" role="img" aria-label="Photo of toned abdominal muscles" style="background:linear-gradient(135deg,#5a3020,#b0724f 50%,#3a2015)"></div><div class="wall-text">Sed adipiscing convallis rhoncis consequat. Nunc semfelis [...]</div></div>
  </div>
</aside>

<aside class="abs panel" style="top:919px;height:139px">
  <h2 class="bar">Snapvault</h2>
  <div class="snaps">
    <div><i role="img" aria-label="Fitness photo" style="background:linear-gradient(135deg,#c8703a,#e4a070)"></i></div>
    <div><i role="img" aria-label="Fitness photo" style="background:linear-gradient(135deg,#ddd,#8a4a7a)"></i></div>
    <div><i role="img" aria-label="Fitness photo" style="background:linear-gradient(135deg,#c87040,#333)"></i></div>
    <div><i role="img" aria-label="Fitness photo" style="background:linear-gradient(135deg,#a55030,#d8b090)"></i></div>
    <div><i role="img" aria-label="Fitness photo" style="background:linear-gradient(135deg,#eee,#b07060)"></i></div>
    <div><i role="img" aria-label="Fitness photo" style="background:linear-gradient(135deg,#cfc6b0,#b08050)"></i></div>
    <div><i role="img" aria-label="Fitness photo" style="background:linear-gradient(135deg,#2a4a4a,#9ab0b0)"></i></div>
    <div><i role="img" aria-label="Fitness photo" style="background:linear-gradient(135deg,#fff,#c07050)"></i></div>
  </div>
</aside>

<footer class="abs footer"></footer>
<div class="abs foot-links">Home |&nbsp; About us &nbsp;|&nbsp; LatestNews &nbsp;|&nbsp; Team &nbsp;|&nbsp; Gallery &nbsp;|&nbsp; Mbership | &nbsp;Classes | &nbsp;Member LogIn &nbsp;|&nbsp; Contact Us &nbsp;| Location</div>
<div class="abs foot-copy">© Copy right 2014 Ironvale Fitness. All rights reserved</div>
<div class="abs socials">
  <span role="img" aria-label="Chirplo" style="background:#3aa7e0"></span>
  <span role="img" aria-label="Kinwall" style="background:#3b62b5"></span>
  <span role="img" aria-label="Proflow" style="background:#2a7fc4"></span>
  <span role="img" aria-label="Email" style="background:#e8501a"></span>
</div>

</body>
</html>
```